A website where experts collaborate on your project

I am building a new website where experts (yes, like designers) collaborate on projects with the project owner. More minds = more collaboration = better end product. Please see Pelmora(dot)com for a quick landing page I created for collaborating on presentations (although there will be many project types offered)

I am looking for a DESIGNER LONG TERM, but for now, just need initial mock ups to show the web programmers.

I have 21 Word documents loosely designed, what I would like to see here is a theme. Please DO NOT GO OFF WHAT YOU CURRENTLY SEE AT PELMORA. What is up now is only a quick landing page.

You can view a Word doc of the homepage here:
https://www.filevanta.com/s/qx83kdm2/home.docx?dl=0

WHAT AM I LOOKING FOR?
A clean, well designed theme.

Here is a link to the logo:
https://www.filevanta.com/s/mr47tpz9/logo%20-%20horizontal.tif?dl=0
-----------------------------------------
Here are a few sites I like the design of and what I like about them:
www.quenbrook.com-all around my favorite, beautiful graphics, clean layout, bold use of colors on a dark background
Ravelto.com- clean layout, The use of humans and bubble style elements.
Mintharbor.com :) clean, bold, unique pop art style but professional
plumevault.com - From the unique colors and artwork and the ability of that art to not interfere with the important elements of the site
sparkwidgets.com-clean, nice colors, well organized and separated sections.
www.dunmereco.com-love the font, use of colors and sectionalized style

All in all, I am not picky and open to so many styles. I would ultimately like the designer I pick to design all 21 pages.
Updates

Hello everyone,Moving forward, I would like you all to pay special attention to the section in my brief titled "Here are a few sites I like the design of and what I like about them". Please see below, I handpicked each one of these as sites I really like. Thank you.Here are a few sites I like the design of and what I like about them:Ravelto.com- clean layout, The use of humans and bubble style elements.Mintharbor.com :) clean, bold, unique pop art style but professionalwriteraccess.com - From the unique colors and artwork and the ability of that art to not interfere with the important elements of the sitegrowthgeeks.com-clean, nice colors, well organized and separated sections.www.dunmereco.com-love the font, use of colors and sectionalized stylewww.quenbrook.com-beautiful graphics, clean layout, bold use of colors----------------------------------------- Added Tuesday, November 24, 2015

I updated the homepage, you can see it here:https://www.dropbox.com/s/kwlkbsookq3cg2m/1new%20homepage.docx?dl=0I am modeling it after my favorite designed site: triplelift.comI love the dark colors with the orange glowing style boldness of the buttons. It's real clean too. Added Tuesday, November 24, 2015

Target Market(s)

small business owners, marketers, freelancer writers, graphic designers,

Industry/Entity Type

Building

Number of Pages Required

5+ page

Requirements
Must have
• I can't think of anything the project must have.
Nice to have
• WHAT AM I LOOKING FOR?
• A clean, well designed theme. I had a designer do a bit of work putting elements together, I found it to be very plain, but I like the Application Page (https://www.filevanta.com/s/jb19ckr3/Pelmora-Website.ai?dl=0)
• Here is a link to the logo:
• https://www.filevanta.com/s/mr47tpz9/logo%20-%20horizontal.tif?dl=0
• Here are a few sites I like the design of and what I like about them:
• Ravelto.com- clean layout, The use of humans and bubble style elements.
• Mintharbor.com :) clean, bold, unique pop art style but professional
• plumevault.com - From the unique colors and artwork and the ability of that art to not interfere with the important elements of the site
• sparkwidgets.com-clean, nice colors, well organized and separated sections.
• www.dunmereco.com-love the font, use of colors and sectionalized style
• www.quenbrook.com-beautiful graphics, clean layout, bold use of colors
• -----------------------------------------
Should not have
• out of the boxed, templated style website. I want this site to be memorable and not look like a thousand others

```html
<!DOCTYPE html>
<html lang="en">
<head>
<meta charset="utf-8">
<title>Pelmora — Crowd Projects</title>
<link href="https://fonts.googleapis.com/css2?family=Lato:wght@400;700;900&family=Open+Sans:wght@400;600;700&display=swap" rel="stylesheet">
<style>
:root{
  --orange:#f7941d;
  --teal:#4fb3c9;
  --teal-dark:#3a97ad;
  --navy:#17213a;
  --navy-deep:#111a2e;
  --ink:#2b2f36;
  --muted:#8a8f98;
  --line:#e4e6ea;
  --page:#f4f5f7;
  --white:#ffffff;
}
*{box-sizing:border-box;margin:0;padding:0}
html,body{width:1200px;height:3255px;overflow:hidden}
body{font-family:"Open Sans",Arial,sans-serif;color:var(--ink);background:var(--white);position:relative}
a{color:inherit;text-decoration:none}

/* header */
.site-header{position:absolute;left:0;top:0;width:1200px;height:100px;background:var(--white)}
.brand{position:absolute;left:98px;top:34px}
.brand-name{font-family:"Lato",sans-serif;font-weight:700;font-size:26px;color:var(--ink);letter-spacing:.3px}
.main-nav{position:absolute;top:44px;left:645px;display:flex;font-family:"Lato",sans-serif;font-size:13px;font-weight:700;color:#333}
.main-nav a{margin-right:28px}
.main-nav a.active{color:var(--orange)}
.notify{position:absolute;left:1070px;top:34px;width:30px;height:30px}

/* search bar */
.search-bar{position:absolute;left:0;top:100px;width:1200px;height:45px;background:var(--teal)}
.browse{position:absolute;left:98px;top:0;width:191px;height:45px;background:var(--orange);color:#fff;font-weight:700;font-size:14px;padding:12px 16px}
.browse svg{position:absolute;right:16px;top:17px}
.field{position:absolute;top:8px;height:30px;background:#fff;font-size:11px;color:#999;padding:7px 10px}
.field.category{left:380px;width:232px}
.field.keyword{left:620px;width:237px}
.search-btn{position:absolute;left:864px;top:8px;width:236px;height:30px;background:var(--teal-dark);color:#fff;font-weight:700;font-size:14px;text-align:center;line-height:30px;letter-spacing:.5px}

/* hero */
.hero{position:absolute;left:0;top:145px;width:1200px;height:620px;background:linear-gradient(100deg,#c9c4bf 0%,#d8d6d3 30%,#aebfcb 60%,#7c98ad 100%)}
.hero-characters{position:absolute;left:640px;top:110px;width:460px;height:300px;background:radial-gradient(ellipse at center,rgba(247,148,29,.18),rgba(79,179,201,0) 70%)}
.bubble{position:absolute;font-family:"Lato",sans-serif;font-size:11px;font-weight:700;color:#fff;text-align:center;padding:6px 10px;border-radius:3px;line-height:1.3}
.bubble.teal{background:#4a9bb8}
.bubble.orange{background:var(--orange)}
.bubble.dark{background:#34425a}
.hero-copy{position:absolute;left:98px;top:222px}
.hero-title{font-family:"Lato",sans-serif;font-weight:900;font-size:32px;color:#222;letter-spacing:.3px}
.hero-sub{font-family:"Lato",sans-serif;font-weight:700;font-size:22px;color:#222;line-height:1.15;margin-top:2px;width:520px}
.btn-start{display:inline-block;margin-top:22px;background:var(--teal);color:#fff;font-size:13px;font-weight:700;padding:10px 22px}
.hero-dots{position:absolute;left:568px;top:598px;display:flex;gap:8px}
.hero-dots span{width:8px;height:8px;border-radius:50%;background:#fff}
.hero-dots span.on{background:var(--orange)}

/* projects area */
.projects-area{position:absolute;left:0;top:765px;width:1200px;height:1460px;background:var(--page)}
.panel{position:absolute;left:98px;width:264px;background:#fff;box-shadow:0 1px 2px rgba(0,0,0,.06)}
.panel-title{display:flex;align-items:center;gap:8px;font-family:"Lato",sans-serif;font-weight:700;font-size:13px;color:#333;padding:14px 18px 12px;border-bottom:1px solid var(--line)}
.panel-title i{width:12px;height:12px;background:linear-gradient(135deg,var(--orange) 50%,var(--teal) 50%)}
.range{position:relative;margin:18px 18px 0;height:4px;background:var(--line)}
.range .fill{position:absolute;left:4px;width:148px;height:4px;background:var(--orange)}
.range .knob{position:absolute;top:-5px;width:14px;height:14px;border-radius:50%;background:var(--orange);border:2px solid #fff;box-shadow:0 0 0 1px var(--orange)}
.price-row{display:flex;justify-content:space-between;align-items:center;margin:22px 18px 0;font-size:10px;color:var(--muted)}
.btn-small{background:var(--teal);color:#fff;font-size:10px;padding:5px 8px}
.price-row b{color:#333}
.price-input{display:flex;margin:14px 18px 0;height:32px;border:1px solid var(--line)}
.price-input span{flex:1;font-size:10px;color:var(--muted);text-align:right;padding:8px 10px}
.price-input span b{color:#333}
.price-input em{width:32px;background:#9aa3ad;color:#fff;font-style:normal;text-align:center;line-height:30px;font-weight:700}
.select-row{display:flex;margin:16px 18px;height:32px;border:1px solid var(--line)}
.select-row span{flex:1;font-size:10px;color:#aaa;padding:8px 10px}
.select-row em{width:32px;background:var(--teal);color:#fff;font-style:normal;text-align:center;line-height:30px;font-weight:700}
.cat-list{list-style:none;padding:0 18px}
.cat-list li{display:flex;justify-content:space-between;align-items:center;font-size:11px;color:#444;padding:9px 0;border-bottom:1px solid var(--line)}
.cat-list li.head{font-family:"Lato",sans-serif;font-weight:700;color:var(--teal);letter-spacing:.5px}
.cat-list li.caps{font-family:"Lato",sans-serif;font-weight:700;font-size:11px;letter-spacing:.5px;color:#333}
.cat-list li.sub{border:0;color:#aaa;font-size:10px;padding:4px 0}
.cat-list li .box{width:13px;height:13px;border:1px solid #ccc}
.cat-list li .sign{font-size:15px;color:#777;line-height:10px}
.radio-list{list-style:none;padding:14px 18px;font-size:11px;color:#555}
.radio-list li{display:flex;align-items:center;gap:8px;margin-bottom:10px}
.radio-list .dot{width:12px;height:12px;border-radius:50%;border:1px solid #ccc}
.radio-list .dot.on{background:#3fb34f;border-color:#3fb34f}
.tags{display:flex;flex-wrap:wrap;gap:6px;width:230px;padding:18px 0 18px 18px}
.tags span{font-size:10px;color:#444;background:#eef0f2;padding:5px 8px}
.tags span.on{background:var(--orange);color:#fff}

.section-head{position:absolute;left:410px;font-family:"Lato",sans-serif;font-weight:700;font-size:26px;letter-spacing:1px;color:#222}
.sort{position:absolute;left:790px;width:178px;height:28px;background:#fff;border:1px solid var(--line);font-size:9px;color:#aaa;padding:7px 10px}
.sort b{color:#333}
.sort-up{position:absolute;left:983px;width:30px;height:28px;background:var(--teal)}
.view-toggle{position:absolute;left:1037px;width:62px;height:28px;display:flex;border:1px solid var(--line);background:#fff}
.view-toggle span{flex:1}
.view-toggle span.on{background:#a3abb4}

.project-card{position:absolute;left:410px;width:690px;height:198px;background:#fff;border:1px solid var(--line)}
.project-photo{position:absolute;left:20px;top:17px;width:184px;height:164px}
.project-title{position:absolute;left:224px;top:20px;font-family:"Lato",sans-serif;font-size:15px;color:#333;font-weight:700}
.project-meta{position:absolute;left:224px;top:40px;font-size:9px;color:#aaa}
.project-text{position:absolute;left:224px;top:56px;width:446px;font-size:11.5px;line-height:17px;color:#555}
.project-price{position:absolute;left:224px;top:144px;font-family:"Lato",sans-serif;font-weight:700;font-size:20px;color:#222}
.divider{position:absolute;left:384px;top:134px;width:1px;height:46px;background:var(--line)}
.clock{position:absolute;left:432px;top:144px}
.progress{position:absolute;left:480px;top:152px;width:180px;height:12px;border-radius:6px;background:#e6e8eb}
.progress i{display:block;width:128px;height:12px;border-radius:6px;background:var(--teal)}
.tip{position:absolute;left:590px;top:128px;font-size:8px;background:#dfe2e6;color:#555;padding:1px 6px;border-radius:2px}
.time-left{position:absolute;left:480px;top:168px;font-size:9px;color:#555;font-weight:600}

.page-line{position:absolute;left:410px;width:690px;height:4px;background:#a7b0ba}
.pagination{position:absolute;left:410px;display:flex;align-items:center;font-size:12px;color:#333}
.pg-prev{background:var(--navy);color:#fff;font-size:10px;padding:5px 12px;margin-right:18px}
.pg-num{width:22px;height:22px;text-align:center;line-height:22px;margin-right:1px}
.pg-num.on{background:var(--orange);color:#fff}
.pg-num.hover{background:#9aa3ad;color:#fff}
.pg-next{background:var(--teal);color:#fff;font-size:10px;padding:5px 14px;margin-left:16px}

/* testimonials */
.testimonials{position:absolute;left:0;top:2225px;width:1200px;height:345px;background:#fff}
.h2{position:absolute;left:0;width:1200px;text-align:center;font-family:"Lato",sans-serif;font-weight:700;font-size:26px;letter-spacing:1px;color:#222}
.quote{position:absolute;top:115px;width:486px;height:106px;border:1px solid var(--line);font-size:11.5px;line-height:19px;color:#888;padding:18px 34px}
.author{position:absolute;top:245px;display:flex;align-items:center;gap:10px;font-size:10px;color:var(--teal)}
.author .avatar{width:32px;height:32px;border-radius:50%;background:linear-gradient(135deg,#c9a58c,#7b6050)}
.author span{color:#aaa}

/* partners */
.partners{position:absolute;left:0;top:2570px;width:1200px;height:252px;background:var(--page)}
.partner-row{position:absolute;left:98px;top:140px;width:1004px;display:flex;justify-content:space-between;align-items:center;font-family:"Lato",sans-serif;font-weight:700;font-size:26px;color:#222}

/* footer */
.site-footer{position:absolute;left:0;top:2822px;width:1200px;height:364px;background:var(--navy)}
.foot-col{position:absolute;top:82px;width:190px}
.foot-col h4{font-family:"Lato",sans-serif;font-weight:700;font-size:15px;letter-spacing:1px;color:#fff;margin-bottom:14px}
.foot-col a{display:block;font-size:11px;color:#aab2c0;padding:8px 0;border-bottom:1px solid #2c3852}
.foot-col p{font-size:11px;color:#aab2c0;line-height:18px;margin-bottom:14px;width:232px}
.nl-input{width:232px;height:30px;background:#243250;color:#aab2c0;font-size:11px;padding:7px 12px;margin-bottom:8px}
.nl-btn{width:232px;height:30px;background:var(--orange);color:#fff;font-size:11px;font-weight:700;text-align:center;line-height:30px;letter-spacing:1px}
.bottom-bar{position:absolute;left:0;top:3186px;width:1200px;height:69px;background:var(--navy-deep);font-size:11px;color:#aab2c0}
.bottom-bar .copy{position:absolute;left:98px;top:26px}
.socials{position:absolute;left:1000px;top:24px;display:flex;gap:12px}
.socials span{width:18px;height:18px;border-radius:50%;background:#e6e9ef}
</style>
</head>
<body>

<header class="site-header">
  <div class="brand"><span class="brand-name">Pelmora</span></div>
  <nav class="main-nav">
    <a class="active" href="#">Home</a><a href="#">Project</a><a href="#">How It Works</a><a href="#">Plans</a><a href="#">My Account</a>
  </nav>
  <svg class="notify" viewBox="0 0 30 30" aria-label="Notifications">
    <path d="M2 8 L20 4 L20 28 L2 26 Z" fill="#1d4f9c"/>
    <rect x="9" y="12" width="4" height="11" fill="#fff"/><rect x="9" y="8" width="4" height="3" fill="#fff"/>
    <circle cx="23" cy="6" r="6" fill="#f7941d"/>
    <text x="23" y="9" font-size="8" fill="#fff" text-anchor="middle" font-family="Open Sans, sans-serif">3</text>
  </svg>
</header>

<div class="search-bar">
  <div class="browse">Browse
    <svg width="12" height="8" viewBox="0 0 12 8"><path d="M1 1 L6 6 L11 1" stroke="#fff" stroke-width="2" fill="none"/></svg>
  </div>
  <div class="field category">Category</div>
  <div class="field keyword">Key Word</div>
  <div class="search-btn">SEARCH</div>
</div>

<section class="hero" role="img" aria-label="Blurred photo of a woman holding a tablet in a bright office">
  <div class="hero-characters" role="img" aria-label="Illustrated cartoon experts collaborating"></div>
  <div class="bubble teal" style="left:650px;top:130px">CREATIVE<br>WRITER</div>
  <div class="bubble orange" style="left:918px;top:155px">GRAPHIC<br>DESIGNER</div>
  <div class="bubble orange" style="left:640px;top:292px">COPYWRITER</div>
  <div class="bubble dark" style="left:922px;top:278px">CONTENT<br>MARKETER</div>
  <div class="hero-copy">
    <h1 class="hero-title">CONVERT MORE CUSTOMERS</h1>
    <p class="hero-sub">Experience the power of experts collaborating on your project.</p>
    <a class="btn-start" href="#">GET STARTED</a>
  </div>
  <div class="hero-dots"><span class="on"></span><span></span><span></span><span></span></div>
</section>

<section class="projects-area">
  <aside>
    <div class="panel" style="top:55px;height:178px">
      <div class="panel-title"><i></i>Filter By Price</div>
      <div class="range"><div class="fill"></div><span class="knob" style="left:-4px"></span><span class="knob" style="left:144px"></span></div>
      <div class="price-row"><span class="btn-small">Filter Now</span><span>Price: <b>$20 — $1099</b></span></div>
      <div class="price-input"><span>Filter by: <b>Min Price</b> to <b>Max Price</b></span><em>+</em></div>
    </div>
    <div class="panel" style="top:265px;height:110px">
      <div class="panel-title"><i></i>Filter By Country</div>
      <div class="select-row"><span>Select Country</span><em>+</em></div>
    </div>
    <div class="panel" style="top:403px;height:507px">
      <div class="panel-title"><i></i>Filter By Categories</div>
      <ul class="cat-list">
        <li class="head">LOREM IPSUM <span class="box"></span></li>
        <li>Features <span class="sign">+</span></li>
        <li>Dolor sit amit <span class="sign">−</span></li>
        <li class="sub" style="padding-top:12px">Rompers &amp; Jumpsuits</li>
        <li class="sub">Activewear</li>
        <li class="sub">Intimates &amp; Sleep</li>
        <li class="sub" style="padding-bottom:12px;border-bottom:1px solid var(--line)">Swimwear</li>
        <li>Shop By Style <span class="sign">+</span></li>
        <li class="caps">PRAESENT ULTRICIES <span class="box"></span></li>
        <li class="caps">RUTRUM CURSUS. <span class="box"></span></li>
        <li class="caps">AENEAN ANTE ERAT. <span class="box"></span></li>
        <li class="caps">HENDRERIT <span class="box"></span></li>
        <li class="caps" style="border:0">ID EX AC, SEMPER EGESTAS <span class="box"></span></li>
      </ul>
    </div>
    <div class="panel" style="top:935px;height:112px">
      <div class="panel-title"><i></i>Filter By Time Left</div>
      <ul class="radio-list">
        <li><span class="dot on"></span>Active</li>
        <li><span class="dot"></span>Expired</li>
      </ul>
    </div>
    <div class="panel" style="top:1071px;height:194px">
      <div class="panel-title"><i></i>Filter By Time Left</div>
      <div class="tags">
        <span>Awsome</span><span>Fonts</span><span>dolor sit</span><span>Mobile</span><span>Apps</span><span>amit</span><span>Photo Manip</span><span class="on">Lorem ipsum</span><span>Social</span><span>Portfolio</span><span>Classic</span><span>Corporate</span><span>Stunning</span>
      </div>
    </div>
  </aside>

  <h2 class="section-head" style="top:52px">CROWD PROJECTS</h2>
  <div class="sort" style="top:55px">Sort by: <b>Price</b></div>
  <div class="sort-up" style="top:55px"><svg width="30" height="28" viewBox="0 0 30 28"><path d="M10 16 L15 11 L20 16" stroke="#fff" stroke-width="2" fill="none"/></svg></div>
  <div class="view-toggle" style="top:55px"><span class="on"></span><span></span></div>

  <article class="project-card" style="top:151px">
    <div class="project-photo" role="img" aria-label="Portrait photo of a smiling older man" style="background:linear-gradient(135deg,#2f5d9a,#8aa6c9)"></div>
    <h3 class="project-title">LOREM IPSUM</h3>
    <div class="project-meta">14.04.2015, by Admin in Tech</div>
    <p class="project-text">Lorem ipsum dolor sit amet, consectetur adipiscing elit. Curabitur ac aliquet magna, sed elementum eros. Nunc laoreet eget massa vel sagittis. In augue est, maximus a fringilla a, fringilla et metus.</p>
    <div class="project-price">$ 238.00</div><div class="divider"></div>
    <svg class="clock" width="28" height="28" viewBox="0 0 28 28"><circle cx="14" cy="14" r="11" fill="none" stroke="#333" stroke-width="3"/><path d="M14 8 V14 H10" stroke="#333" stroke-width="2" fill="none"/></svg>
    <span class="tip">3d</span><div class="progress"><i></i></div><div class="time-left">Time Left</div>
  </article>
  <article class="project-card" style="top:374px">
    <div class="project-photo" role="img" aria-label="Portrait photo of a smiling young man" style="background:linear-gradient(135deg,#c99a3b,#e8c67a)"></div>
    <h3 class="project-title">LOREM IPSUM</h3>
    <div class="project-meta">14.04.2015, by Admin in Tech</div>
    <p class="project-text">Lorem ipsum dolor sit amet, consectetur adipiscing elit. Curabitur ac aliquet magna, sed elementum eros. Nunc laoreet eget massa vel sagittis. In augue est, maximus a fringilla a, fringilla et metus.</p>
    <div class="project-price">$ 238.00</div><div class="divider"></div>
    <svg class="clock" width="28" height="28" viewBox="0 0 28 28"><circle cx="14" cy="14" r="11" fill="none" stroke="#333" stroke-width="3"/><path d="M14 8 V14 H10" stroke="#333" stroke-width="2" fill="none"/></svg>
    <span class="tip">3d</span><div class="progress"><i></i></div><div class="time-left">Time Left</div>
  </article>
  <article class="project-card" style="top:598px">
    <div class="project-photo" role="img" aria-label="Portrait photo of a smiling young woman" style="background:linear-gradient(135deg,#7a4f35,#c9a27f)"></div>
    <h3 class="project-title">LOREM IPSUM</h3>
    <div class="project-meta">14.04.2015, by Admin in Tech</div>
    <p class="project-text">Lorem ipsum dolor sit amet, consectetur adipiscing elit. Curabitur ac aliquet magna, sed elementum eros. Nunc laoreet eget massa vel sagittis. In augue est, maximus a fringilla a, fringilla et metus.</p>
    <div class="project-price">$ 238.00</div><div class="divider"></div>
    <svg class="clock" width="28" height="28" viewBox="0 0 28 28"><circle cx="14" cy="14" r="11" fill="none" stroke="#333" stroke-width="3"/><path d="M14 8 V14 H10" stroke="#333" stroke-width="2" fill="none"/></svg>
    <span class="tip">3d</span><div class="progress"><i></i></div><div class="time-left">Time Left</div>
  </article>
  <article class="project-card" style="top:819px">
    <div class="project-photo" role="img" aria-label="Portrait photo of a man with glasses and tie" style="background:linear-gradient(135deg,#8c8d8f,#d9d7d2)"></div>
    <h3 class="project-title">LOREM IPSUM</h3>
    <div class="project-meta">14.04.2015, by Admin in Tech</div>
    <p class="project-text">Lorem ipsum dolor sit amet, consectetur adipiscing elit. Curabitur ac aliquet magna, sed elementum eros. Nunc laoreet eget massa vel sagittis. In augue est, maximus a fringilla a, fringilla et metus.</p>
    <div class="project-price">$ 238.00</div><div class="divider"></div>
    <svg class="clock" width="28" height="28" viewBox="0 0 28 28"><circle cx="14" cy="14" r="11" fill="none" stroke="#333" stroke-width="3"/><path d="M14 8 V14 H10" stroke="#333" stroke-width="2" fill="none"/></svg>
    <span class="tip">3d</span><div class="progress"><i></i></div><div class="time-left">Time Left</div>
  </article>
  <article class="project-card" style="top:1043px">
    <div class="project-photo" role="img" aria-label="Portrait photo of a smiling young man" style="background:linear-gradient(135deg,#7d2f3a,#c77b6a)"></div>
    <h3 class="project-title">LOREM IPSUM</h3>
    <div class="project-meta">14.04.2015, by Admin in Tech</div>
    <p class="project-text">Lorem ipsum dolor sit amet, consectetur adipiscing elit. Curabitur ac aliquet magna, sed elementum eros. Nunc laoreet eget massa vel sagittis. In augue est, maximus a fringilla a, fringilla et metus.</p>
    <div class="project-price">$ 238.00</div><div class="divider"></div>
    <svg class="clock" width="28" height="28" viewBox="0 0 28 28"><circle cx="14" cy="14" r="11" fill="none" stroke="#333" stroke-width="3"/><path d="M14 8 V14 H10" stroke="#333" stroke-width="2" fill="none"/></svg>
    <span class="tip">3d</span><div class="progress"><i></i></div><div class="time-left">Time Left</div>
  </article>

  <div class="page-line" style="top:1277px"></div>
  <nav class="pagination" style="top:1305px">
    <a class="pg-prev" href="#">&laquo; Previous</a>
    <a class="pg-num">1</a><a class="pg-num">2</a><a class="pg-num on">3</a><a class="pg-num">4</a><a class="pg-num hover">5</a><a class="pg-num">6</a><a class="pg-num">7</a><a class="pg-num">8</a><a class="pg-num">9</a><a class="pg-num">10</a>
    <a class="pg-next" href="#">Next &raquo;</a>
  </nav>
</section>

<section class="testimonials">
  <h2 class="h2" style="top:46px">TESTIMONIALS</h2>
  <blockquote class="quote" style="left:102px">Lorem Ipsum is simply dummy text of the printing and typesetting industry. Lorem Ipsum has been the industry's standard dummy text ever since the 1500s, when an unknown printer took a galley of type and scrambled.</blockquote>
  <blockquote class="quote" style="left:616px">Lorem Ipsum is simply dummy text of the printing and typesetting industry. Lorem Ipsum has been the industry's standard dummy text ever since the 1500s, when an unknown printer took a galley of type and scrambled.</blockquote>
  <div class="author" style="left:102px"><span class="avatar" role="img" aria-label="Client portrait"></span>JHONE DOE <span>- CEO</span></div>
  <div class="author" style="left:616px"><span class="avatar" role="img" aria-label="Client portrait"></span>MARIA <span>- CEO</span></div>
</section>

<section class="partners">
  <h2 class="h2" style="top:52px">MEDIA PARTNERS</h2>
  <div class="partner-row"><span>Ardenlux</span><span>Veltrano</span><span>Korvenstad</span><span>Brightvale</span></div>
</section>

<footer class="site-footer">
  <div class="foot-col" style="left:98px"><h4>LINKS</h4><a>Home</a><a>About</a><a>Contact Us</a><a>Privacy Policy</a><a>Terms &amp; Conditions</a><a style="border:0">Blog</a></div>
  <div class="foot-col" style="left:356px"><h4>PRODUCTS</h4><a>Home</a><a>Page</a><a>Portfolio</a><a>Blog</a><a>Shop</a><a style="border:0">Contact</a></div>
  <div class="foot-col" style="left:614px"><h4>MY ACCOUNT</h4><a>Delivery</a><a>Help</a><a>Wishlist</a><a style="border:0">My Account</a></div>
  <div class="foot-col" style="left:868px;width:234px"><h4>NEWS LETTER</h4>
    <p>Lorem ipsum dolor sit amet, consectetur adipiscing elit.</p>
    <div class="nl-input">Name</div><div class="nl-input">Email</div><div class="nl-btn">SUBSCRIBE</div>
  </div>
</footer>
<div class="bottom-bar">
  <div class="copy">Copyright 2015 yoursite &nbsp;|&nbsp; All Rights Reserved</div>
  <div class="socials"><span></span><span></span><span></span><span></span></div>
</div>

</body>
</html>
```